Business Card Design For A Cajun Seafood Restaurant

We are opening a cajun seafood restaurant in a week. We mainly serve cajun seafood which is orginally from Louisiana. We want design on both sides of a business card. I have menu on the website. You can go to www.reednkettle.example to check out our menu.

Restaurant name: Reed N' Kettle
Phone: +1 (555) 304-7712
Address: 48206 Ludlow Row, #7, Bexmoor Flats, Ca90000
Email: reednkettle@mailbox.example
Website: www.reednkettle.example

Maybe add social media icons (facebook, instagram) if looks nice on the business card.
facebook.com/reednkettle
instagram.com/reednkettle or @reednkettle

Attached is the logo and other business card samples that I like.

```html
<!DOCTYPE html>
<html lang="en">
<head>
<meta charset="utf-8">
<title>Reed N' Kettle — Business Card</title>
<link rel="stylesheet" href="https://fonts.googleapis.com/css2?family=Source+Sans+3:wght@400;600;700&display=swap">
<style>
  :root {
    --backdrop: #9b9b9b;
    --card: #eeeef0;
    --ink: #111111;
    --orange: #e8701e;
    --gold: #e3b62b;
    --white: #ffffff;
    --crab-main: #e0692a;
    --crab-light: #f0a23c;
  }
  html, body {
    margin: 0;
    padding: 0;
    width: 1105px;
    height: 1200px;
    overflow: hidden;
    background: var(--backdrop);
    font-family: "Source Sans 3", "Helvetica Neue", Arial, sans-serif;
  }
  .card {
    position: absolute;
    left: 182px;
    width: 746px;
    height: 426px;
    background: var(--card);
  }
  .card--front { top: 119px; }
  .card--back { top: 635px; }

  .mascot {
    position: absolute;
    border-radius: 46% 46% 40% 40%;
    background: radial-gradient(ellipse at 50% 35%, var(--crab-light) 0%, var(--crab-main) 65%, rgba(224,105,42,0) 72%);
  }
  .card--front .mascot { left: 273px; top: 29px; width: 200px; height: 192px; }
  .card--back .mascot { left: 301px; top: 79px; width: 166px; height: 154px; }

  .contact-panel {
    position: absolute;
    left: 28px;
    top: 206px;
    width: 690px;
    height: 197px;
  }
  .contact-panel__frame { position: absolute; inset: 0; }
  .contact-panel__text {
    position: absolute;
    inset: 0;
    text-align: center;
    color: var(--white);
    font-size: 19px;
  }
  .holder {
    position: absolute;
    left: 0; right: 0;
    top: 38px;
    margin: 0;
    font-weight: 400;
    font-size: 24px;
    color: var(--orange);
    letter-spacing: 0.3px;
  }
  .holder__role { color: var(--gold); font-size: 20px; margin-left: 6px; }
  .line { position: absolute; left: 0; right: 0; margin: 0; }
  .line--address { top: 79px; }
  .line--reach { top: 109px; }
  .line--web { top: 137px; }
  .icon { display: inline-block; vertical-align: -2px; margin-right: 5px; }
  .gap { margin-left: 6px; }

  .brand {
    position: absolute;
    left: 0; right: 0;
    top: 238px;
    margin: 0;
    text-align: center;
    font-size: 40px;
    font-weight: 700;
    color: var(--orange);
    letter-spacing: 1px;
  }
  .socials {
    position: absolute;
    left: 0; right: 0;
    top: 362px;
    text-align: center;
    font-size: 21px;
    color: var(--ink);
  }
  .social { display: inline-flex; align-items: center; gap: 7px; margin: 0 3px; }
  .social__dot {
    width: 26px; height: 26px;
    border-radius: 50%;
    background: var(--orange);
    display: inline-block;
  }
</style>
</head>
<body>

<section class="card card--front">
  <div class="mascot" role="img" aria-label="Cartoon crab mascot holding an ear of corn overhead"></div>

  <div class="contact-panel">
    <svg class="contact-panel__frame" width="690" height="197" viewBox="0 0 690 197" aria-hidden="true">
      <path d="M16 0 H674 V16 H690 V181 H674 V197 H16 V181 H0 V16 H16 Z" fill="var(--ink)"/>
      <path d="M22 6 H668 V22 H684 V175 H668 V191 H22 V175 H6 V22 H22 Z" fill="none" stroke="var(--white)" stroke-width="1.5"/>
    </svg>
    <div class="contact-panel__text">
      <p class="holder">DALE HARTWELL &nbsp;-<span class="holder__role">CEO/Founder</span></p>
      <p class="line line--address">48206 Ludlow Row, #7, Bexmoor Flats, Ca90000</p>
      <p class="line line--reach"><svg class="icon" width="17" height="17" viewBox="0 0 24 24" aria-hidden="true"><path fill="var(--orange)" d="M6.6 10.8a15 15 0 0 0 6.6 6.6l2.2-2.2c.3-.3.7-.4 1-.2 1.1.4 2.3.6 3.6.6.6 0 1 .4 1 1V20c0 .6-.4 1-1 1A17 17 0 0 1 3 4c0-.6.4-1 1-1h3.5c.6 0 1 .4 1 1 0 1.3.2 2.5.6 3.6.1.3 0 .7-.2 1z"/></svg>+1 (555) 304-7712<span class="gap"><svg class="icon" width="17" height="13" viewBox="0 0 24 18" aria-hidden="true"><rect x="0" y="0" width="24" height="18" rx="2" fill="var(--orange)"/><path d="M1 1 L12 10 L23 1" fill="none" stroke="var(--ink)" stroke-width="2"/></svg>reednkettle@mailbox.example</span></p>
      <p class="line line--web"><svg class="icon" width="17" height="17" viewBox="0 0 24 24" aria-hidden="true"><circle cx="12" cy="12" r="10" fill="var(--orange)"/><path d="M2 12h20M12 2c3 3 3 17 0 20M12 2c-3 3-3 17 0 20" fill="none" stroke="var(--ink)" stroke-width="1.5"/></svg>www.reednkettle.example</p>
    </div>
  </div>
</section>

<section class="card card--back">
  <div class="mascot" role="img" aria-label="Cartoon crab mascot holding an ear of corn overhead"></div>
  <p class="brand">Reed N' Kettle</p>
  <div class="socials">
    <span class="social"><span class="social__dot" aria-hidden="true"></span>reednkettle</span>
    <span class="social"><span class="social__dot" aria-hidden="true"></span>@reednkettle</span>
  </div>
</section>

</body>
</html>
```